Verodex business card

Business card for sustainable investment company called "Verodex". Verodex is an exchange platform selling carbon credits between buyers and sellers. Carbon Credits are an environmental commodity for reducing global carbon emissions.

the card should obviously have our logo and the theme should be sustainability/environment mixed with a trading platform.

Contact Information for Business Card

Logo, Name, Title, Phone, Email

Colors
0054AA
0677BA
7BADD7
CADEEF
E8F1F8
0094D4
00A9DD
6FCCEA
C7EBF8
E9F6FB
00AB8E
00BBA5
67D7C9
C6EFE9
E9F9F6
59FF00
82FF00
B8FF75
E3FFCB
F4FFEA

```html
<!DOCTYPE html>
<html lang="en">
<head>
<meta charset="utf-8">
<title>Verodex business card</title>
<link href="https://fonts.googleapis.com/css2?family=Outfit:wght@400;500;600;700&display=swap" rel="stylesheet">
<style>
  :root {
    --page-bg: #e4e4e4;
    --navy-deep: #1b2b45;
    --navy-soft: #304761;
    --ink: #1e2f4d;
    --brand-teal: #4fb3d0;
    --brand-blue: #3a72bc;
    --card-white: #f1f1f1;
    --white: #f7f7f7;
  }
  * { margin: 0; padding: 0; box-sizing: border-box; }
  html, body {
    width: 1200px; height: 1200px; overflow: hidden;
    background: var(--page-bg);
    font-family: "Outfit", sans-serif;
  }
  .stage { position: relative; width: 1200px; height: 1200px; }
  .card {
    position: absolute; left: 234px; width: 731px; height: 417px;
  }
  .card--front {
    top: 160px;
    background: linear-gradient(200deg, var(--navy-soft) 0%, var(--navy-deep) 75%);
  }
  .card--back {
    top: 632px;
    background: linear-gradient(200deg, #f5f5f5 0%, #e8e8e8 100%);
    color: var(--ink);
  }
  .brand {
    position: absolute; display: flex; align-items: center;
    font-weight: 600; letter-spacing: 0.5px; line-height: 1;
  }
  .brand__dot {
    border-radius: 50%; background: var(--brand-blue); flex: none;
  }
  .card--front .brand {
    left: 0; right: 0; top: 174px; justify-content: center; gap: 22px;
    color: var(--white); font-size: 62px;
  }
  .card--front .brand__dot { width: 58px; height: 58px; }
  .card--back .brand {
    right: 53px; top: 56px; gap: 16px; font-size: 42px; color: var(--ink);
  }
  .card--back .brand__dot { width: 40px; height: 40px; }
  .person { position: absolute; left: 49px; top: 190px; }
  .person__name {
    font-size: 37px; font-weight: 700; color: #3f8dc4; line-height: 1;
  }
  .person__title { font-size: 20px; font-weight: 400; margin-top: 10px; }
  .divider {
    position: absolute; left: 50px; top: 273px; width: 628px; height: 2px;
    background: linear-gradient(90deg, var(--brand-teal), var(--brand-blue));
  }
  .contacts {
    position: absolute; left: 49px; top: 291px; list-style: none;
    font-size: 20px; line-height: 27.5px;
  }
  .contacts li { display: flex; align-items: center; gap: 8px; }
  .contacts svg { width: 16px; height: 16px; flex: none; }
  .office {
    position: absolute; right: 53px; top: 293px; text-align: right;
    font-size: 20px; line-height: 27.5px;
  }
  .office__title { font-weight: 600; }
</style>
</head>
<body>
<main class="stage">
  <section class="card card--front">
    <div class="brand"><span class="brand__dot"></span><span class="brand__name">VERODEX</span></div>
  </section>

  <section class="card card--back">
    <div class="brand"><span class="brand__dot"></span><span class="brand__name">VERODEX</span></div>

    <div class="person">
      <p class="person__name">Mark Halden</p>
      <p class="person__title">Sales Representative</p>
    </div>

    <div class="divider"></div>

    <ul class="contacts">
      <li>
        <svg viewBox="0 0 16 16" aria-hidden="true"><path fill="#3a7fc0" d="M3.5 1.5l2.2 2.6-1.3 1.6c.9 2 2.4 3.5 4.4 4.4l1.6-1.3 2.6 2.2-1.3 2.2C6.6 13 3 9.4 1.3 2.8z"/></svg>
        <span>+36 30 555 0142</span>
      </li>
      <li>
        <svg viewBox="0 0 16 16" aria-hidden="true"><rect x="1" y="3" width="14" height="10" rx="1" fill="#3a7fc0"/><path d="M1.5 3.8L8 9l6.5-5.2" fill="none" stroke="#eef3f8" stroke-width="1.2"/></svg>
        <span>szerviz@verodex.com</span>
      </li>
      <li>
        <svg viewBox="0 0 16 16" aria-hidden="true"><g fill="none" stroke="#3a7fc0" stroke-width="1.4"><circle cx="8" cy="8" r="6.5"/><ellipse cx="8" cy="8" rx="2.8" ry="6.5"/><path d="M1.5 8h13"/></g></svg>
        <span>www.verodex.com</span>
      </li>
    </ul>

    <address class="office" style="font-style:normal">
      <p class="office__title">Verodex Head Office</p>
      <p>Budapest XI.</p>
      <p>Fenyves utca 12.</p>
    </address>
  </section>
</main>
</body>
</html>
```